Web Design Project - Shipping Industry

Goals and Objectives
The objective of the new website is to create a more modern look and feel. The site will also allow for a more effective means of communicating with members while providing the public with information and developments in the local, regional and international shipping industry.
Scope
The website will highlight the history of the organisation inclusive of text and photographs. It will take visitors through the years from beginning to present. Information on the history of the shipping industry will also be included.
It will feature current articles on the organisation, its members and stakeholders in the shipping industry. Member information as well as pertinent details regarding the organisation’s subsidiaries will be documented for the website.
Information as it relates to shipping statistics, case studies, laws and regulations, international treaties and trade documents, shipping terms, careers in shipping, job opportunities, training opportunities, information for shippers including port listing and trade lanes will be main features of the content for the website.
The Association’s community involvement, industry calendar events and related links relevant industry members will also be featured.
Target Market
• The General Public;
• Members of the organization;
• Shipping Industry Stakeholders (local, regional and international);
• Tertiary students conducting research.
• Potential employees
• Potential Business Partners
Best Practice Bench Marketing
The following websites are being looked at:
• Korvel Quayworks - http://www.korvelquayworks.example/ (preferred look)
• Tessaly Maritime Association - http://www.tma-freight.example/ (like image transition on main page)
• Drovna - http://www.drovna.example (professional look)
• PLW - http://www.pelworth.example (preferred color: blue in logo)
• Quillo - http://www.quillo.example/electronics/tv-video-audio/ (preferred look for links page: image + short text below + visit site link)
Expected Result
• 3 - 5 pages which must include: [1] main page [2] standard page [3] links page

```html
<!DOCTYPE html>
<html lang="en">
<head>
<meta charset="utf-8">
<title>The Shipping Association of Pelworth – About Us</title>
<link href="https://fonts.googleapis.com/css2?family=Arimo:wght@400;700&family=Questrial&family=Tinos&display=swap" rel="stylesheet">
<style>
:root{
  --blue-deep:#0a3aa6;
  --blue-mid:#1f5fd0;
  --blue-light:#4f8ae6;
  --ink:#333;
  --link:#0b3e9e;
  --heading:#0d47b0;
  --rule:#c9c9c9;
  --band:#eeeeee;
  --white:#fff;
}
*{margin:0;padding:0;box-sizing:border-box}
html,body{width:1200px;height:900px;overflow:hidden}
body{
  background:radial-gradient(ellipse at 50% 40%, var(--blue-light) 0%, var(--blue-mid) 40%, var(--blue-deep) 85%);
  font-family:"Arimo",Arial,sans-serif;color:var(--ink);position:relative;
}
.page{position:absolute;left:195px;top:0;width:805px;height:847px;background:var(--white)}
.brand{position:absolute;left:45px;top:14px;display:flex;align-items:center;gap:14px}
.brand-mark{width:40px;height:40px;border-radius:50%;background:var(--blue-mid)}
.brand-name{font-family:"Tinos",serif;font-size:23px;color:#3b6fd0}
.search{position:absolute;left:587px;top:35px;width:168px;height:18px;display:flex}
.search-field{flex:1;border:1px solid #ccc;background:#f6f6f6;font-size:9px;color:#aaa;padding:3px 10px;font-style:italic}
.search-btn{width:23px;background:var(--blue-mid);display:flex;align-items:center;justify-content:center}
.nav{position:absolute;left:44px;top:70px;width:711px;height:31px;background:linear-gradient(#f6f6f6,#e6e6e6);display:flex;align-items:center;font-family:"Questrial",sans-serif;font-size:9.5px;color:var(--link)}
.nav a{color:var(--link);text-decoration:none;padding:0 16px;border-right:1px solid #ccc;line-height:14px}
.nav a:last-child{border:none}
.nav a.active{background:var(--blue-deep);color:#fff;line-height:23px;border:none;padding:0 19px}
.crumb{position:absolute;left:52px;top:114px;width:700px;font-size:9.5px;border-bottom:1px solid #ddd;padding-bottom:7px;display:flex;align-items:center;gap:6px}
.crumb span{color:var(--link)}
.main{position:absolute;left:51px;top:150px;width:497px;font-size:10.5px;line-height:15.4px}
.main h1,.acc h2{font-family:"Questrial",sans-serif;font-weight:400;color:var(--heading);font-size:13.5px}
.main h1{margin-bottom:6px}
.main p{margin-bottom:15px}
.acc{border-top:1px dashed var(--rule);display:flex;justify-content:space-between;align-items:center;height:33px;width:492px}
.acc.last{border-bottom:1px dashed var(--rule)}
.acc-body{padding-top:22px;width:497px}
.acc-body ul{list-style:none;margin-top:-11px;margin-bottom:24px}
.acc-body li{padding-left:18px;position:relative}
.acc-body li:before{content:"";position:absolute;left:4px;top:4px;border-left:4px solid var(--blue-deep);border-top:3.5px solid transparent;border-bottom:3.5px solid transparent}
.side{position:absolute;left:568px;top:148px;width:187px;font-size:10.5px}
.side a{display:block;height:24px;line-height:24px;padding-left:20px;color:var(--link);text-decoration:none;background:linear-gradient(90deg,#fff,#efefef 50%,#fff)}
.side a.current{color:#2a6bd8;position:relative}
.side a.current:before{content:"";position:absolute;left:8px;top:7px;border-left:4px solid var(--blue-deep);border-top:3.5px solid transparent;border-bottom:3.5px solid transparent}
.login{position:absolute;left:570px;top:337px;width:186px;height:54px;border:1px solid #ccc;display:flex;align-items:center;gap:10px;padding:4px}
.login-photo{width:58px;height:46px;background:linear-gradient(#dde4ef,#8fa2bf)}
.login span{font-family:"Questrial",sans-serif;color:var(--heading);font-size:13px}
.social{position:absolute;left:582px;top:418px;display:flex;gap:22px}
.social i{display:block;width:36px;height:24px;border-radius:3px}
.partners{position:absolute;left:43px;top:741px;width:712px;height:75px;background:linear-gradient(90deg,#eee,#f9f9f9 50%,#eee);display:flex;align-items:center}
.partners h3{font-family:"Questrial",sans-serif;font-weight:400;color:var(--heading);font-size:12.5px;line-height:15px;width:80px;padding-left:5px}
.partner{font-family:"Arimo",sans-serif;font-weight:700;font-size:12px;color:var(--link);width:140px;text-align:center}
.arrow{color:#bbb;font-size:26px;width:28px;text-align:center}
.footer{position:absolute;left:197px;top:847px;width:803px;height:53px;display:flex;align-items:center;justify-content:space-between;color:#fff}
.footer small{font-size:9.5px}
.footer .brand-f{display:flex;align-items:center;gap:6px;font-family:"Tinos",serif;font-size:18px}
.footer .brand-f i{width:34px;height:34px;border-radius:50%;background:#6c9be8;display:block}
</style>
</head>
<body>
<div class="page">
  <div class="brand"><div class="brand-mark"></div><div class="brand-name">The shipping association of Pelworth</div></div>
  <div class="search"><div class="search-field">Search</div><div class="search-btn"><svg width="10" height="10" viewBox="0 0 10 10"><circle cx="4" cy="4" r="3" fill="none" stroke="#fff" stroke-width="1.6"/><line x1="6.2" y1="6.2" x2="9" y2="9" stroke="#fff" stroke-width="1.8"/></svg></div></div>
  <nav class="nav">
    <a href="#">HOME</a><a href="#" class="active">ABOUT US</a><a href="#">PRODUCTS</a><a href="#">SERVICES</a><a href="#">NEWS</a><a href="#">SUPPORT</a><a href="#">PARTNERS</a><a href="#">CUSTOMERS</a><a href="#">CONTACT</a>
  </nav>
  <div class="crumb"><svg width="11" height="10" viewBox="0 0 11 10"><path d="M5.5 0L0 5h1.5v5h3V7h2v3h3V5H11z" fill="#3b6fd0"/></svg>Home &gt; <span>About Us</span></div>

  <div class="main">
    <h1>THE SHIPPING ASSOCIATION OF PELWORTH</h1>
    <p>As a 71-year-old organization, the Shipping Association of Pelworth, (PLW) has charted the developments in the Maritime Sector in Pelworth since the late 1930s, and has been an active participant in ensuring that Pelworth's Shipping Industry remains competitive and viable for the long haul.</p>
    <p>With registered offices close to the Port of Harrowmere, the Association has recorded steady growth in its membership (which now number 78), spanning shipping agents, terminal operators, stevedoring companies, hauliers, NVOCCs, ship owners and operators, and providers of business support services to the Port Community.</p>
    <div class="acc"><h2>HOW THE PLW OPERATES</h2><svg width="16" height="16" viewBox="0 0 16 16"><circle cx="8" cy="8" r="7" fill="#fff" stroke="#888"/><path d="M4.5 10h7L8 5z" fill="#777"/></svg></div>
    <div class="acc-body">
      <p>Registered as a Trade Union, one of the primary functions of the Association is the manangement of certain categories of labour on the Port. In addition, the Association acts on behalf of its members in initiatives to advance industrial relations, training, security, information technology, and to establish uniform standards and rates of remuneration for port labour within the Maritime Sector. The PLW, like other Trade Associations, has a strong advocacy and lobbying remit, and liaises with Government agencies and bodies, as well as other private sector organizations to ensure the continued development of the Shipping Industry in the island.</p>
      <p>Apart from its lobbying functions, the Secretariat provides:</p>
      <ul>
        <li>Specialized training opportunities for its members,</li>
        <li>General information on developments in the industry both locally and abroad</li>
        <li>Specialized information packages</li>
        <li>Project support to membership groups</li>
        <li>Community outreach programmes on behalf of the membership</li>
      </ul>
    </div>
    <div class="acc"><h2>INFORMATION TECHNOLOGY</h2><svg width="16" height="16" viewBox="0 0 16 16"><circle cx="8" cy="8" r="7" fill="#fff" stroke="#888"/><path d="M4.5 6h7L8 11z" fill="#777"/></svg></div>
    <div class="acc"><h2>SECURITY</h2><svg width="16" height="16" viewBox="0 0 16 16"><circle cx="8" cy="8" r="7" fill="#fff" stroke="#888"/><path d="M4.5 6h7L8 11z" fill="#777"/></svg></div>
    <div class="acc last"><h2>REGIONAL INVOLVEMENT</h2><svg width="16" height="16" viewBox="0 0 16 16"><circle cx="8" cy="8" r="7" fill="#fff" stroke="#888"/><path d="M4.5 6h7L8 11z" fill="#777"/></svg></div>
  </div>

  <aside class="side">
    <a href="#" class="current">About Us</a>
    <a href="#">President's Profile</a>
    <a href="#">Committee Members</a>
    <a href="#">Vacancies</a>
    <a href="#">Member Directory</a>
    <a href="#">Photo Gallery</a>
    <a href="#">Services</a>
  </aside>
  <div class="login"><div class="login-photo" role="img" aria-label="Photo of two port managers reviewing plans"></div><span>MEMBER LOGIN</span></div>
  <div class="social"><i style="background:#2f4f9a"></i><i style="background:#2aa6dd"></i><i style="background:#f07a22"></i></div>

  <div class="partners">
    <h3>OUR<br>PARTNERS</h3>
    <div class="arrow">‹</div>
    <div class="partner">Bayline Cargo</div>
    <div class="partner">Harrowmere Wharves</div>
    <div class="partner">Tidecrest Freight</div>
    <div class="partner">Solvara Line</div>
    <div class="arrow">›</div>
  </div>
</div>
<footer class="footer">
  <small>© The Shipping Association Of Pelworth 2012, All Right Reserved</small>
  <div class="brand-f"><i></i>The shipping association of Pelworth</div>
</footer>
</body>
</html>
```